Law Offices business card

Hi there, I'll need business card for the Law Offices of Colin Matheny. The information must convey his strategic approach and quick resolution to complex business litigation needs. Please emphasize Civil Litigation, Corporate Law, Business Governance and Real Estate Law. Colin has over 25 years of experience in these fields.The card should be modern and edgy and the message should be clear. Please consult his current website for ideas.

```html
<!DOCTYPE html>
<html lang="en">
<head>
<meta charset="utf-8">
<title>Law Offices of Colin Matheny — Business Card</title>
<link href="https://fonts.googleapis.com/css2?family=Open+Sans:wght@400;600;700&display=swap" rel="stylesheet">
<style>
  :root {
    --bg: #2b2b2d;
    --card: #050505;
    --lavender: #a9a6c4;
    --red: #e02a25;
    --text-light: #b7b4cf;
  }
  * { margin: 0; padding: 0; box-sizing: border-box; }
  html, body { width: 1200px; height: 900px; overflow: hidden; background: var(--bg); }
  body { position: relative; font-family: "Open Sans", Arial, sans-serif; }

  .card {
    position: absolute;
    width: 700px; height: 400px;
    left: 250px;
    background: var(--card);
    overflow: hidden;
    box-shadow: 0 14px 30px rgba(0,0,0,.55);
  }
  .card--front { top: 34px; }
  .card--back  { top: 466px; }
  .card svg.bands { position: absolute; inset: 0; }

  .wordmark {
    position: absolute; left: 44px; top: 62px;
    display: flex; align-items: center; gap: 12px;
    color: var(--lavender);
    font-weight: 600;
    line-height: 1.05;
  }
  .wordmark__mark { width: 16px; height: 16px; background: var(--red); flex: none; }
  .wordmark__text { font-size: 15px; letter-spacing: .06em; text-transform: uppercase; }
  .wordmark__text span { display: block; font-size: 38px; letter-spacing: 0; text-transform: none; }

  .services {
    position: absolute; right: 40px; top: 168px;
    text-align: right; list-style: none;
    color: var(--text-light); font-size: 14px; letter-spacing: .03em; line-height: 1.4;
  }
  .experience {
    position: absolute; right: 40px; top: 286px;
    color: var(--red); font-size: 12px; font-weight: 600; letter-spacing: .08em;
  }

  .person { position: absolute; right: 42px; top: 122px; text-align: right; }
  .person__name { color: var(--lavender); font-weight: 700; font-size: 26px; letter-spacing: .01em; }
  .person__title { color: var(--red); font-size: 12px; font-weight: 600; letter-spacing: .08em; }

  .address {
    position: absolute; right: 40px; top: 226px; text-align: right;
    color: var(--text-light); font-size: 14px; line-height: 1.35; font-style: normal;
  }

  .contacts { position: absolute; left: 44px; top: 232px; list-style: none; }
  .contacts li {
    display: flex; align-items: center; gap: 10px;
    color: var(--text-light); font-size: 15px; line-height: 1.4;
  }
  .contacts svg { width: 12px; height: 12px; flex: none; }
</style>
</head>
<body>

  <section class="card card--front" aria-label="Business card, front">
    <svg class="bands" width="700" height="400" viewBox="0 0 700 400">
      <polygon points="0,330 292,330 312,344 312,400 0,400" fill="var(--lavender)"/>
      <polygon points="300,330 700,330 700,342 316,342" fill="var(--red)"/>
    </svg>
    <div class="wordmark">
      <div class="wordmark__mark"></div>
      <div class="wordmark__text">Law Offices of<span>Colin Matheny, PA</span></div>
    </div>
    <ul class="services">
      <li>CIVIL LITIGATION</li>
      <li>CORPORATE LAW</li>
      <li>BUSINESS GOVERNANCE</li>
      <li>REAL ESTATE LAW</li>
    </ul>
    <p class="experience">OVER 25 YEARS OF EXPERIENCE</p>
  </section>

  <section class="card card--back" aria-label="Business card, back">
    <svg class="bands" width="700" height="400" viewBox="0 0 700 400">
      <rect x="678" y="116" width="22" height="44" fill="var(--red)"/>
      <line x1="44" y1="212" x2="664" y2="212" stroke="var(--lavender)" stroke-width="1.5"/>
      <polygon points="486,290 700,290 700,334 470,334" fill="var(--lavender)"/>
      <polygon points="0,362 462,362 454,374 0,374" fill="var(--red)"/>
    </svg>
    <div class="wordmark">
      <div class="wordmark__mark"></div>
      <div class="wordmark__text">Law Offices of<span>Colin Matheny, PA</span></div>
    </div>
    <div class="person">
      <div class="person__name">COLIN MATHENY</div>
      <div class="person__title">ATTORNEY</div>
    </div>
    <address class="address">118 Harbor Lane<br>Coral Cove, FL 33019</address>
    <ul class="contacts">
      <li><svg viewBox="0 0 12 12"><path d="M2.5 1h2l1 3-1.5 1a7 7 0 0 0 3 3l1-1.5 3 1v2a1 1 0 0 1-1 1A10 10 0 0 1 1.5 2a1 1 0 0 1 1-1z" fill="var(--red)"/></svg>555-301-4827</li>
      <li><svg viewBox="0 0 12 12"><rect x="2" y="4" width="8" height="6" rx="1" fill="var(--red)"/><rect x="3" y="1" width="6" height="3" fill="var(--red)"/></svg>555-301-4860</li>
      <li><svg viewBox="0 0 12 12"><rect x="1" y="2.5" width="10" height="7" fill="none" stroke="var(--red)" stroke-width="1.2"/><path d="M1 3l5 4 5-4" fill="none" stroke="var(--red)" stroke-width="1.2"/></svg>colin@mathenylaw.com</li>
      <li><svg viewBox="0 0 12 12"><circle cx="6" cy="6" r="5" fill="none" stroke="var(--red)" stroke-width="1.2"/><path d="M1 6h10M6 1c-3 3-3 7 0 10M6 1c3 3 3 7 0 10" fill="none" stroke="var(--red)" stroke-width="1"/></svg>www.mathenylaw.com</li>
    </ul>
  </section>

</body>
</html>
```